Design a New Business Card for Our Company

We are looking for fresh, unique, and a modern business card that reflects our roots as digital marketing agency focused on SEM.

Industry/Entity Type

Marketing

Contact Information for Business Card

looking for very unique out of the box designs. clean and modern that compliments our logo

Requirements
Must have
• colors should match our logo
• Front should have name, address, email, and phone/fax of the person, phone/fax are the same number
• back should have our url

```html
<!DOCTYPE html>
<html lang="en">
<head>
<meta charset="utf-8">
<title>Brightpath Media – Business Card</title>
<link rel="stylesheet" href="https://fonts.googleapis.com/css2?family=Arimo:wght@400;700&display=swap">
<style>
  :root {
    --backdrop: #2b2b2d;
    --card-white: #fbfbfb;
    --card-shade: #e4e6e9;
    --brand-blue: #3f6fb0;
    --deep-blue: #1f4f98;
    --band-grey: #58595c;
    --soft-blue: #b9cbe0;
    --soft-grey: #cfd1d4;
    --ink-grey: #6d6e71;
    --band-text: #f2f2f2;
  }
  * { box-sizing: border-box; margin: 0; padding: 0; }
  html, body { width: 1200px; height: 997px; overflow: hidden; }
  body {
    background: var(--backdrop);
    font-family: "Arimo", Arial, sans-serif;
    position: relative;
  }
  .card {
    position: absolute;
    width: 520px;
    height: 300px;
    border-radius: 18px;
    overflow: hidden;
    background: linear-gradient(160deg, var(--card-white) 0%, var(--card-shade) 100%);
    box-shadow: 0 18px 40px rgba(0,0,0,.55);
  }
  .card-front { left: 90px; top: 150px; }
  .card-back { left: 590px; top: 500px; }
  .card-art { position: absolute; inset: 0; width: 100%; height: 100%; }

  .brand {
    position: absolute;
    display: flex;
    align-items: center;
    gap: 10px;
    color: var(--brand-blue);
    font-weight: 700;
    white-space: nowrap;
  }
  .brand-dot { border-radius: 50%; background: var(--brand-blue); }
  .card-front .brand { right: 34px; top: 40px; font-size: 26px; }
  .card-front .brand-dot { width: 18px; height: 18px; }

  .holder { position: absolute; left: 34px; top: 86px; }
  .holder-name { color: var(--brand-blue); font-size: 20px; font-weight: 700; }
  .holder-role { color: var(--ink-grey); font-size: 12px; font-weight: 700; margin-top: 2px; }

  .contact-list {
    position: absolute;
    left: 30px;
    bottom: 18px;
    list-style: none;
    color: var(--band-text);
    font-size: 12.5px;
    line-height: 18px;
  }
  .contact-list li { display: flex; align-items: flex-start; gap: 8px; }
  .contact-icon { width: 14px; height: 14px; margin-top: 2px; flex: none; }
  .contact-list .address { max-width: 260px; }

  .pattern-field { position: absolute; left: 0; top: 0; width: 300px; height: 300px; }
  .card-back .brand { left: 56px; top: 82px; font-size: 40px; gap: 14px; }
  .card-back .brand-dot { width: 34px; height: 34px; }
  .site-url {
    position: absolute;
    right: 24px;
    bottom: 50px;
    color: var(--band-text);
    font-size: 13px;
    font-weight: 700;
    letter-spacing: 2.5px;
    white-space: nowrap;
    transform: rotate(-5deg);
    transform-origin: right bottom;
  }
</style>
</head>
<body>

<section class="card card-front" aria-label="Business card front">
  <svg class="card-art" viewBox="0 0 520 300" aria-hidden="true">
    <path d="M0 175 Q 200 100 520 95 L520 300 L0 300 Z" fill="var(--brand-blue)"/>
    <path d="M0 185 Q 210 110 520 103 L520 300 L0 300 Z" fill="var(--card-white)"/>
    <path d="M0 193 Q 220 118 520 111 L520 300 L0 300 Z" fill="var(--band-grey)"/>
  </svg>
  <div class="brand"><span class="brand-dot"></span>Brightpath Media</div>
  <div class="holder">
    <p class="holder-name">Clara Weston</p>
    <p class="holder-role">Director</p>
  </div>
  <ul class="contact-list">
    <li>
      <svg class="contact-icon" viewBox="0 0 14 14"><circle cx="7" cy="7" r="7" fill="var(--brand-blue)"/><path d="M4.3 3.6l1.4-.4.8 1.9-.9.7a5 5 0 0 0 2.6 2.6l.7-.9 1.9.8-.4 1.4c-3.6.2-6.3-2.5-6.1-6.1z" fill="#fff"/></svg>
      <span>0561230948</span>
    </li>
    <li>
      <svg class="contact-icon" viewBox="0 0 14 14"><circle cx="7" cy="7" r="7" fill="var(--brand-blue)"/><rect x="4.5" y="3" width="5" height="3" fill="#fff"/><rect x="3" y="6" width="8" height="4" rx="1" fill="#fff"/></svg>
      <span>0178804126</span>
    </li>
    <li>
      <svg class="contact-icon" viewBox="0 0 14 14"><circle cx="7" cy="7" r="7" fill="var(--brand-blue)"/><rect x="3" y="4.5" width="8" height="5.5" fill="#fff"/><path d="M3 4.5l4 3 4-3" fill="none" stroke="var(--brand-blue)" stroke-width="1"/></svg>
      <span>hello@brightpathmedia.com</span>
    </li>
    <li>
      <svg class="contact-icon" viewBox="0 0 14 14"><circle cx="7" cy="7" r="7" fill="var(--brand-blue)"/><path d="M7 11.5S4 8 4 6a3 3 0 0 1 6 0c0 2-3 5.5-3 5.5z" fill="#fff"/><circle cx="7" cy="6" r="1" fill="var(--brand-blue)"/></svg>
      <span class="address">Suite 4, 218 Harbor Road, Kelsey, Ontario Canada</span>
    </li>
  </ul>
</section>

<section class="card card-back" aria-label="Business card back">
  <div class="pattern-field" role="img" aria-label="Soft pattern of scattered translucent blue and grey circles"
       style="background: radial-gradient(circle at 40% 55%, var(--soft-blue) 0%, var(--soft-grey) 45%, rgba(255,255,255,0) 75%); opacity:.6;"></div>
  <svg class="card-art" viewBox="0 0 520 300" aria-hidden="true">
    <path d="M100 300 Q 280 170 520 140 L520 300 Z" fill="var(--deep-blue)"/>
    <path d="M110 300 Q 290 180 520 150 L520 300 Z" fill="var(--card-white)"/>
    <path d="M120 300 Q 300 190 520 160 L520 300 Z" fill="var(--band-grey)"/>
  </svg>
  <div class="brand"><span class="brand-dot"></span>Brightpath Media</div>
  <p class="site-url">www.brightpathmed.com</p>
</section>

</body>
</html>
```